Trucking/service truck *Updated

Cards for a trucking company. Company transfers logs to saw mills. We are looking for something edgy, modern and fun. It's very limited when it comes to trucking business card choices. Plus the owner also runs an on-site service truck. He has 20+ years mechanic experience.
Colors are open. Favorites are orange & purple, but not must have. We really want to emphasize trust, dependability and knowledge with a bright, attention getter.
On card:
Fennimore & Fennimore
Dale Fennimore - Owner/Manager/Maintenance 555-214-0937
Tamra Fennimore -Office Administration/Bookkeeping 555-362-1748
4172 Maple Bend Rd.
Gilmer, Texas 70000
555-490-2613 - Office
Updates
Just a thought. Do you think you can combine the Taurus and Pisces signs? And put in the corner, or on the back or anything really? Thanks! You all or doing fantastic!

```html
<!DOCTYPE html>
<html lang="en">
<head>
<meta charset="utf-8">
<title>Fennimore &amp; Fennimore — Business Card</title>
<link rel="stylesheet" href="https://fonts.googleapis.com/css2?family=Exo+2:wght@400;500;600&display=swap">
<style>
  :root {
    --page-bg: #ecebe8;
    --card-white: #ffffff;
    --frame-red: #f2301b;
    --band-blue-dark: #1d4f9c;
    --band-blue-light: #3a79d0;
    --ink: #4a4a4a;
    --rule-grey: #9a9a9a;
    --brand-blue: #2a5ea8;
  }
  * { box-sizing: border-box; margin: 0; padding: 0; }
  html, body {
    width: 1200px; height: 677px; overflow: hidden;
    background: var(--page-bg);
    font-family: "Exo 2", Arial, sans-serif;
  }
  .stage {
    width: 1200px; height: 677px;
    display: flex; align-items: center; justify-content: center;
  }
  .card {
    position: relative;
    width: 340px; height: 594px;
    background: var(--card-white);
    border: 10px solid var(--frame-red);
    box-shadow: 0 10px 30px rgba(0,0,0,.18);
  }
  .brand {
    position: absolute; top: 96px; left: 0; right: 0;
    display: flex; align-items: center; justify-content: center; gap: 10px;
  }
  .brand-dot {
    width: 14px; height: 14px; border-radius: 50%;
    background: var(--frame-red); flex: none;
  }
  .brand-name {
    font-size: 20px; font-weight: 500; color: var(--brand-blue);
    letter-spacing: .2px;
  }
  .name-band {
    position: absolute; top: 196px; left: 0; right: 0; height: 78px;
    background: linear-gradient(90deg, var(--band-blue-dark), var(--band-blue-light));
    color: var(--card-white);
    display: flex; flex-direction: column; justify-content: center;
    align-items: flex-end; padding-right: 24px; gap: 3px;
    text-transform: uppercase; letter-spacing: 1px;
  }
  .person-name { font-size: 22px; font-weight: 600; line-height: 1.1; }
  .person-role { font-size: 13px; font-weight: 500; line-height: 1.2; }
  .contacts {
    position: absolute; top: 306px; left: 26px; right: 20px;
    list-style: none; display: flex; flex-direction: column; gap: 13px;
  }
  .contact {
    display: flex; align-items: center; gap: 12px;
    font-size: 13.5px; color: var(--ink); white-space: nowrap;
  }
  .contact-icon {
    width: 22px; height: 22px; border-radius: 4px; flex: none;
    background: var(--frame-red);
    display: flex; align-items: center; justify-content: center;
  }
  .contact-label { font-weight: 600; }
  .address {
    position: absolute; left: 0; right: 0; top: 472px;
    border-top: 1px solid var(--rule-grey);
    border-bottom: 1px solid var(--rule-grey);
    padding: 14px 20px 14px 26px;
  }
</style>
</head>
<body>
<main class="stage">
  <article class="card">
    <header class="brand">
      <span class="brand-dot"></span>
      <span class="brand-name">Fennimore &amp; Fennimore</span>
    </header>

    <section class="name-band">
      <div class="person-name">Dale Fennimore</div>
      <div class="person-role">Owner / Manager / Maintenance</div>
    </section>

    <ul class="contacts">
      <li class="contact">
        <span class="contact-icon"><svg width="12" height="12" viewBox="0 0 24 24"><path fill="#fff" d="M6.6 10.8a15 15 0 0 0 6.6 6.6l2.2-2.2c.3-.3.7-.4 1-.2 1.1.4 2.3.6 3.6.6.6 0 1 .4 1 1V20c0 .6-.4 1-1 1A17 17 0 0 1 3 4c0-.6.4-1 1-1h3.5c.6 0 1 .4 1 1 0 1.3.2 2.5.6 3.6.1.3 0 .7-.2 1z"/></svg></span>
        <span>555-214-0937 · Office 555-490-2613</span>
      </li>
      <li class="contact">
        <span class="contact-icon"><svg width="12" height="12" viewBox="0 0 24 24"><rect x="6" y="2" width="12" height="20" rx="2" fill="#fff"/><rect x="8" y="5" width="8" height="12" fill="#f2301b"/></svg></span>
        <span><span class="contact-label">Tamra Fennimore</span> 555-362-1748</span>
      </li>
      <li class="contact">
        <span class="contact-icon"><svg width="12" height="12" viewBox="0 0 24 24"><rect x="2" y="5" width="20" height="14" rx="2" fill="#fff"/><path d="M3 6l9 7 9-7" fill="none" stroke="#f2301b" stroke-width="2"/></svg></span>
        <span>dale@fennimorehaul.com</span>
      </li>
      <li class="contact">
        <span class="contact-icon"><svg width="12" height="12" viewBox="0 0 24 24"><circle cx="12" cy="12" r="9" fill="none" stroke="#fff" stroke-width="2"/><path d="M3 12h18M12 3c3 3 3 15 0 18M12 3c-3 3-3 15 0 18" fill="none" stroke="#fff" stroke-width="1.6"/></svg></span>
        <span>www.fennimorehaul.com</span>
      </li>
    </ul>

    <div class="address">
      <div class="contact">
        <span class="contact-icon"><svg width="12" height="12" viewBox="0 0 24 24"><path fill="#fff" d="M12 2a7 7 0 0 0-7 7c0 5 7 13 7 13s7-8 7-13a7 7 0 0 0-7-7zm0 9.5A2.5 2.5 0 1 1 12 6.5a2.5 2.5 0 0 1 0 5z"/></svg></span>
        <span>4172 Maple Bend Rd. Gilmer, Texas 70000</span>
      </div>
    </div>
  </article>
</main>
</body>
</html>
```